Marden Voss Advisory Webpage

I need to transition into a Wordpress website to be able to insert tracking code. This was a HostLark website, but now I'm limited on functionality

Here are requirements: I need to replicate mardenvoss.example

My company is focused in search and placement, consulting and workforce development for the turfgrass and hospitality industry

I'm also looking to integrate the following for a recruiting agency job board.
Multiple Dashboard view
✔ Job map
✔ Demo Content upload
✔ Chat button
✔ CV/Resume builder
✔ Featured job on top
✔ Email Alert
✔ Job bookmark
✔ Job CV package
✔ Social media Login
✔ SEO set up
✔ Plugin installation
✔ Featured jobs
✔ Payment gateway integration and set up
✔ Responsive design
Updates

Went on vacation/holiday

Target Market(s)

Golf and turfgrass businesses; as well as candidates for those companies

Industry/Entity Type

Turfgrass and Golf Industry

Coding

Coded - Design and coding required

Font styles to use
Sans Serif

Colors

Designer to choose colors to be used in the design.

Requirements
Must have
• Functionality of HostLark Web Design builder, Chat box capability, pop up capability, scheduling/appointment booking integration, ability to upload videos similar to my current website, e-commerce capabilities
Nice to have
• Everything to integrate "recruiting agency" aspect to collect information from potential candidates

```html
<!DOCTYPE html>
<html lang="en">
<head>
<meta charset="utf-8">
<title>Marden Voss Advisory</title>
<link rel="stylesheet" href="https://fonts.googleapis.com/css2?family=Poppins:ital,wght@0,400;0,500;0,600;0,700;1,400&display=swap">
<style>
:root{
  --green:#3f5245;
  --green-mid:#4d5e51;
  --ink:#2b3a31;
  --text:#5b6460;
  --light:#eef1f4;
  --white:#ffffff;
  --footer:#151b25;
  --chat:#7fb8dc;
}
*{box-sizing:border-box;margin:0;padding:0}
html,body{width:1200px;height:5310px;overflow:hidden}
body{font-family:'Poppins',sans-serif;color:var(--text);background:var(--white);position:relative}
.pill{display:inline-flex;align-items:center;gap:6px;border-radius:22px;font-weight:500;font-size:14px;height:40px;padding:0 26px;white-space:nowrap}
.pill-dark{background:var(--green);color:var(--white)}
.arrow{width:12px;height:12px;border-radius:50%;background:currentColor;display:inline-block;position:relative}
.arrow::after{content:"";position:absolute;left:3px;top:3px;border-left:6px solid var(--green);border-top:3px solid transparent;border-bottom:3px solid transparent}
.pill-white .arrow::after{border-left-color:var(--white)}
.section-title{position:absolute;left:0;width:1200px;text-align:center;font-weight:600;font-size:42px;color:var(--ink);letter-spacing:.5px}
.divider{position:absolute;left:566px;width:68px;height:2px;background:var(--ink)}
.divider::after{content:"";position:absolute;left:29px;top:-4px;width:10px;height:10px;border-radius:50%;background:inherit}

/* header */
.site-header{position:absolute;left:0;top:0;width:1200px;height:130px;background:var(--white)}
.brand{position:absolute;left:88px;top:46px;display:flex;align-items:center;gap:10px}
.brand-mark{width:26px;height:26px;border-radius:50%;background:var(--green)}
.brand-name{font-weight:600;font-size:17px;line-height:20px;color:var(--green);letter-spacing:.5px}
.contact-chip{position:absolute;top:16px;display:flex;align-items:center;gap:10px}
.contact-chip .ico{width:44px;height:44px;border-radius:50%;border:2px solid #cfd3d0;display:flex;align-items:center;justify-content:center}
.contact-chip small{display:block;font-size:11px;color:#777;line-height:14px}
.contact-chip b{font-weight:600;font-size:15px;color:#222}
.quote{position:absolute;left:943px;top:18px;height:44px}
.main-nav{position:absolute;right:100px;top:86px;display:flex;gap:28px;font-weight:500;font-size:14px;color:#1f2a24}

/* hero */
.hero{position:absolute;left:0;top:130px;width:1200px;height:546px;display:flex}
.hero-photo{flex:1;height:100%;border-right:2px solid var(--white)}
.hero-panel{position:absolute;left:265px;top:125px;width:725px;height:295px;background:rgba(70,100,75,.55);border-radius:6px;text-align:center;color:var(--white)}
.hero-panel h1{font-weight:700;font-size:54px;line-height:58px;margin-top:30px;letter-spacing:.5px}
.hero-panel p{font-size:23px;margin-top:12px;letter-spacing:.3px}
.hero-panel .pill{background:var(--white);color:#222;margin-top:18px;height:42px}

/* about */
.about-photo{position:absolute;left:125px;top:783px;width:462px;height:500px;border-radius:70px 0 0 0;background:linear-gradient(160deg,#b9c2c4 0%,#8a958c 45%,#3f4a52 100%)}
.about-blob{position:absolute;left:110px;top:775px;width:100px;height:100px;border-radius:50%;background:var(--green)}
.dots{position:absolute;background-image:radial-gradient(#8d9690 1.6px,transparent 1.8px);background-size:16px 16px}
.about-title{position:absolute;left:660px;top:770px;font-weight:600;font-size:44px;color:var(--ink)}
.about-rule{position:absolute;left:630px;top:844px;width:90px;height:2px;background:var(--ink)}
.about-rule::before{content:"";position:absolute;left:0;top:-4px;width:10px;height:10px;border-radius:50%;background:var(--ink)}
.about-text{position:absolute;left:655px;top:868px;width:445px;font-size:13.5px;line-height:25px;text-align:justify}
.about-text p{margin-bottom:10px}
.about-actions{position:absolute;left:655px;top:1238px;display:flex;gap:28px}
.pill-outline{border:2px solid var(--green);color:#222;background:var(--white)}

/* help */
.help{position:absolute;left:0;top:1395px;width:1200px;height:1843px;background:var(--green-mid)}
.help .section-title{color:var(--white);top:98px}
.help .divider{background:var(--white);top:165px}
.svc-photo{position:absolute;width:482px;height:437px}
.svc-card{position:absolute;width:482px;height:363px;background:var(--white);border-radius:50px 0 50px 0;padding:68px 46px 0 46px}
.svc-card h3{font-weight:600;font-size:22px;color:#1e2822}
.svc-card p{font-size:13.5px;line-height:29px;margin-top:18px;color:#555}
.svc-card .pill{margin-top:20px;height:40px;font-size:13px}

/* testimonials */
.testimonials{position:absolute;left:0;top:3238px;width:1200px;height:655px;background:var(--light)}
.testi{position:absolute;top:194px;width:478px;height:333px;background:var(--white);border-radius:10px;box-shadow:0 4px 10px rgba(0,0,0,.12);text-align:center;padding:0 30px}
.quote-mark{font-family:Georgia,serif;font-weight:700;font-size:96px;line-height:1;color:var(--green);margin-top:30px;height:70px}
.testi blockquote{font-style:italic;font-size:19px;line-height:39px;color:#555;margin-top:14px}
.author{display:flex;justify-content:center;align-items:center;gap:20px;margin-top:14px}
.author .org{font-weight:600;font-size:13px;line-height:14px;color:var(--green);width:110px;text-align:center}
.author .crest{width:46px;height:46px;border-radius:50%;background:#c9b15d}
.author .who{text-align:left;font-size:19px;line-height:30px;color:#222;font-weight:500}
.author .who b{font-weight:600;display:block}
.pager{position:absolute;top:582px;left:560px;display:flex;gap:10px}
.pager i{width:11px;height:11px;border-radius:50%;border:1.5px solid #555;display:block}
.pager i.on{background:#555}

/* news */
.news{position:absolute;left:0;top:3893px;width:1200px;height:657px}
.news-card{position:absolute;background:var(--white);box-shadow:0 2px 10px rgba(0,0,0,.12)}
.news-date{font-size:13px;color:#333;display:flex;align-items:center;gap:5px}
.news-date::before{content:"";width:11px;height:11px;background:#555;border-radius:2px}
.news-card h4{font-weight:600;font-size:19px;line-height:23px;color:#1f2a24;margin-top:6px}
.news-card p{font-size:13px;line-height:27px;color:#444;margin-top:4px}
.news-card p u{color:var(--green)}

/* partners */
.partners{position:absolute;left:0;top:4550px;width:1200px;height:390px}
.partner{position:absolute;top:225px;width:233px;height:116px;background:var(--white);box-shadow:0 2px 8px rgba(0,0,0,.14);display:flex;align-items:center;justify-content:center}

/* footer */
.site-footer{position:absolute;left:0;top:4940px;width:1200px;height:370px;background:var(--footer);color:#e8e8e8}
.foot-brand{position:absolute;left:130px;top:145px;display:flex;align-items:center;gap:10px}
.foot-brand .brand-mark{background:var(--white)}
.foot-brand .brand-name{color:var(--white)}
.socials{position:absolute;left:127px;top:258px;display:flex;gap:16px}
.socials i{width:31px;height:31px;border-radius:50%;border:1.5px solid #aaa;display:block}
.foot-col{position:absolute;top:72px}
.foot-col h5{font-weight:500;font-size:16px;letter-spacing:.5px;margin-bottom:14px;color:var(--white)}
.foot-col li{list-style:none;font-size:13px;line-height:30px}
.foot-contact{display:flex;gap:14px;align-items:center;font-size:13px;line-height:20px;margin-bottom:16px}
.foot-contact .ico{width:34px;height:34px;border-radius:50%;background:#3a4250;display:flex;align-items:center;justify-content:center;flex-shrink:0}
.newsletter{margin-top:14px;width:240px;height:42px;border-radius:21px;background:var(--white);display:flex;align-items:center;justify-content:space-between;padding:0 4px 0 14px;color:#333;font-size:13px}
.newsletter span.go{width:44px;height:34px;border-radius:17px;background:var(--green);display:flex;align-items:center;justify-content:center}
.copyright{position:absolute;left:0;width:1200px;top:332px;text-align:center;font-size:13px}
.chat{position:absolute;left:1100px;top:4870px;width:70px;height:70px;border-radius:50%;background:var(--chat);box-shadow:0 3px 8px rgba(0,0,0,.25);display:flex;align-items:center;justify-content:center;z-index:2}
</style>
</head>
<body>

<header class="site-header">
  <div class="brand"><span class="brand-mark"></span><span class="brand-name">MARDEN VOSS<br>ADVISORY</span></div>
  <div class="contact-chip" style="left:515px">
    <span class="ico"><svg width="18" height="18" viewBox="0 0 24 24"><path d="M6.6 10.8a15 15 0 0 0 6.6 6.6l2.2-2.2a1 1 0 0 1 1-.25 11 11 0 0 0 3.6.6 1 1 0 0 1 1 1V20a1 1 0 0 1-1 1A17 17 0 0 1 3 4a1 1 0 0 1 1-1h3.5a1 1 0 0 1 1 1 11 11 0 0 0 .6 3.6 1 1 0 0 1-.25 1z" fill="#333"/></svg></span>
    <span><small>CALL US</small><b>555.014.2270</b></span>
  </div>
  <div class="contact-chip" style="left:685px">
    <span class="ico"><svg width="20" height="16" viewBox="0 0 24 18"><rect x="1" y="1" width="22" height="16" rx="2" fill="none" stroke="#333" stroke-width="2"/><path d="M1 2l11 8 11-8" fill="none" stroke="#333" stroke-width="2"/></svg></span>
    <span><small>EMAIL</small><b>mvoss.golf@example.com</b></span>
  </div>
  <a class="pill pill-dark quote pill-white">Get a Quote <span class="arrow"></span></a>
  <nav class="main-nav"><span>HOME</span><span>MARDEN VOSS</span><span>WORKFORCE DEVELOPMENT</span><span>NEWS</span><span>CLIENTS</span><span>CONTACT</span></nav>
</header>

<section class="hero">
  <div class="hero-photo" role="img" aria-label="Clubhouse clock on a manicured lawn" style="background:linear-gradient(180deg,#9bb7c9 0%,#6d8a6a 50%,#4d6e3e 100%)"></div>
  <div class="hero-photo" role="img" aria-label="Adirondack chairs overlooking a golf course" style="background:linear-gradient(180deg,#c9d6df 0%,#8ea58a 55%,#6b5a42 100%)"></div>
  <div class="hero-photo" role="img" aria-label="Aerial view of a city park and skyline" style="background:linear-gradient(180deg,#9aa9a3 0%,#4f6a43 50%,#7b7a72 100%)"></div>
  <div class="hero-photo" role="img" aria-label="Golf pin flag over the green" style="background:linear-gradient(180deg,#6aa4d8 0%,#c7d7e4 45%,#5f8a3a 100%);border-right:0"></div>
  <div class="hero-panel">
    <h1>WE CREATE SUSTAINABLE<br>TALENT SOLUTIONS</h1>
    <p>FOR THE TURFGRASS, GREEN AND CLUB INDUSTRIES</p>
    <span class="pill">Schedule Appointment <span class="arrow"></span></span>
  </div>
</section>

<section class="about">
  <div class="dots" style="left:88px;top:1010px;width:22px;height:290px"></div>
  <div class="dots" style="left:88px;top:1290px;width:310px;height:22px"></div>
  <div class="about-blob"></div>
  <div class="about-photo" role="img" aria-label="Portrait of Marden Voss on a golf course"></div>
  <h2 class="about-title">ABOUT MARDEN</h2>
  <div class="about-rule"></div>
  <div class="about-text">
    <p>Marden's passion for the game of golf began at the age of 6. After playing high school golf, Marden attended Northfield State University to study Turfgrass Science. He interned at three top 50 golf courses - Harrow Glen Golf Club, Cedar Ridge Country Club for the 2007 National Pro Championship, and Stonebrook Village Golf Club for the 2008 Heritage Invitational</p>
    <p>Upon graduation he was an Assistant at Ashford Country Club for three years while preparing for the 2010 National Women's Open Championship before earning a Lead Assistant position at Brightwater Golf Club.</p>
    <p>At the age of 27, Marden took over as Golf Course Superintendent at Wrenfield Point Country Club, a 27-hole private facility in Baltimore, Maryland. It was here Marden developed</p>
  </div>
  <div class="about-actions">
    <span class="pill pill-dark">Learn More <span class="arrow"></span></span>
    <span class="pill pill-outline"><svg width="16" height="16" viewBox="0 0 24 24"><circle cx="12" cy="12" r="12" fill="#3f5245"/><path d="M8.5 10.5a8 8 0 0 0 5 5l1.3-1.3 2.2 1v2.3c-6 0-10.5-4.5-10.5-10.5h2.3l1 2.2z" fill="#fff"/></svg>555.014.2270</span>
  </div>
</section>

<section class="help">
  <h2 class="section-title">HOW WE HELP YOU</h2>
  <div class="divider"></div>

  <div class="svc-photo" role="img" aria-label="Empty boardroom with leather chairs" style="left:140px;top:233px;background:linear-gradient(135deg,#d9d6cf 0%,#8d8478 55%,#4a3f35 100%)"></div>
  <div class="svc-card" style="left:578px;top:270px">
    <h3>SEARCH &amp; PLACEMENT</h3>
    <p>Powered by our national presence, unmatched recruiting network and deep search process. We provide search for managerial and executive level positions.</p>
    <span class="pill pill-dark">Learn More <span class="arrow"></span></span>
  </div>

  <div class="svc-photo" role="img" aria-label="Golf course fairway with bunkers and trees" style="left:578px;top:765px;background:linear-gradient(180deg,#b9cfe0 0%,#4f7a35 35%,#6f9a45 70%,#d8d1b5 100%)"></div>
  <div class="svc-card" style="left:140px;top:803px">
    <h3>WORKFOARCE DEVELOPMENT</h3>
    <p>Our customized partnership models allow us to be responsive to your unique needs. Whether you need immediate staff needs, expanded outreach or long-term succession planning, we are pioneers in workforce development for the turfgrass, green and club industries.</p>
    <span class="pill pill-dark">Learn More <span class="arrow"></span></span>
  </div>

  <div class="svc-photo" role="img" aria-label="Speaker at a wooden podium during a conference" style="left:140px;top:1298px;background:linear-gradient(135deg,#2c3f86 0%,#1b2550 45%,#8a5a2e 75%,#3a2c22 100%)"></div>
  <div class="svc-card" style="left:578px;top:1338px">
    <h3>CONSULTING</h3>
    <p>Marden utilizes a proven framework backed by 65-years of data and science to help business partners inspire performance, measure engagement, hire the best talent and design high performing teams.</p>
    <span class="pill pill-dark">Learn More <span class="arrow"></span></span>
  </div>
</section>

<section class="testimonials">
  <h2 class="section-title" style="top:88px">TESTIMONIALS</h2>
  <div class="divider" style="top:157px"></div>
  <div class="testi" style="left:100px">
    <div class="quote-mark">&ldquo;</div>
    <blockquote>Without question, Marden Voss raised the bar with dozens of qualified applicants that fit the end goal criteria.</blockquote>
    <div class="author"><span class="org">RIVERSIDE PARKS TRUST</span><span class="who">Paul Renzetti<b>Director of Landscape</b></span></div>
  </div>
  <div class="testi" style="left:622px">
    <div class="quote-mark">&ldquo;</div>
    <blockquote>The quality and value the facility gets from Marden Voss is off the charts...highly recommended!</blockquote>
    <div class="author"><span class="crest"></span><span class="who">Owen Hartley<b>Head Golf Professional</b></span></div>
  </div>
  <div class="pager"><i></i><i class="on"></i><i></i><i></i></div>
</section>

<section class="news">
  <h2 class="section-title" style="top:82px">LATEST NEWS</h2>
  <div class="divider" style="top:150px"></div>

  <article class="news-card" style="left:100px;top:187px;width:480px;height:400px;padding:12px 12px 0">
    <div role="img" aria-label="Resort clubhouse behind a golf green" style="height:230px;background:linear-gradient(180deg,#c5d9e6 0%,#4f7d3a 45%,#7a5b3e 70%,#5f8f3c 100%)"></div>
    <div style="padding:14px 8px 0">
      <div class="news-date">February 12, 2022</div>
      <h4>Partner Stories - Larkin Valley Golf &amp; Resort</h4>
      <p>Martin Ellery wasn't confident he would be able to make his March 1 deadline when he posted on assistant ... <u>READ MORE</u></p>
    </div>
  </article>

  <article class="news-card" style="left:610px;top:187px;width:490px;height:165px;padding:10px">
    <div role="img" aria-label="Golfer silhouetted at sunset" style="position:absolute;left:10px;top:10px;width:160px;height:145px;background:linear-gradient(180deg,#8ab0c9 0%,#e3a05a 55%,#3a2b22 100%)"></div>
    <div style="position:absolute;left:178px;top:18px;width:300px">
      <div class="news-date">February 12, 2022</div>
      <h4>Looking for a Few Good Assistants</h4>
      <p>Grant Mercer discuss solutions &amp; challenges golf courses face in ... <u>READ MORE</u></p>
    </div>
  </article>

  <article class="news-card" style="left:610px;top:392px;width:490px;height:165px;padding:10px">
    <div role="img" aria-label="Golf hole with lake and trees" style="position:absolute;left:10px;top:10px;width:160px;height:145px;background:linear-gradient(180deg,#b9d0e4 0%,#5a8a3f 45%,#4f7aa0 70%,#6d9a45 100%)"></div>
    <div style="position:absolute;left:178px;top:18px;width:300px">
      <div class="news-date">February 12, 2022</div>
      <h4>Fairway Trade Weekly - Firm &amp; Fast</h4>
      <p>First off, the labor market is tiresome ... and periodically frustrating ... <u>READ MORE</u></p>
    </div>
  </article>
</section>

<section class="partners">
  <h2 class="section-title" style="top:82px">OUR PARTNERS</h2>
  <div class="divider" style="top:150px"></div>
  <div class="partner" style="left:100px"><svg width="60" height="60" aria-label="Partner club badge" role="img"><circle cx="30" cy="30" r="26" fill="#2d4f8f"/></svg></div>
  <div class="partner" style="left:355px"><svg width="60" height="60" aria-label="Partner club badge" role="img"><circle cx="30" cy="30" r="26" fill="none" stroke="#2f6b3f" stroke-width="5"/></svg></div>
  <div class="partner" style="left:610px"><svg width="60" height="60" aria-label="Partner club badge" role="img"><rect x="6" y="6" width="48" height="48" rx="6" fill="#2f6b3f"/></svg></div>
  <div class="partner" style="left:865px"><svg width="60" height="60" aria-label="Partner club badge" role="img"><circle cx="30" cy="30" r="26" fill="#d8662b"/></svg></div>
</section>

<div class="chat"><svg width="30" height="26" viewBox="0 0 30 26"><path d="M3 2h24a2 2 0 0 1 2 2v14a2 2 0 0 1-2 2H12l-6 5v-5H3a2 2 0 0 1-2-2V4a2 2 0 0 1 2-2z" fill="#fff"/><circle cx="9" cy="11" r="2" fill="#7fb8dc"/><circle cx="15" cy="11" r="2" fill="#7fb8dc"/><circle cx="21" cy="11" r="2" fill="#7fb8dc"/></svg></div>

<footer class="site-footer">
  <div class="foot-brand"><span class="brand-mark"></span><span class="brand-name">MARDEN VOSS<br>ADVISORY</span></div>
  <div class="socials" aria-label="Social links"><i></i><i></i><i></i><i></i></div>
  <div class="foot-col" style="left:353px">
    <h5>QUICK LINKS</h5>
    <ul><li>Home</li><li>Marden Voss</li><li>Workforce Development</li><li>Latest News</li><li>Recent Clients</li><li>Contact</li></ul>
  </div>
  <div class="foot-col" style="left:580px;width:260px">
    <h5>CONTACT US</h5>
    <div class="foot-contact"><span class="ico"><svg width="14" height="18" viewBox="0 0 14 18"><path d="M7 0a7 7 0 0 1 7 7c0 5-7 11-7 11S0 12 0 7a7 7 0 0 1 7-7z" fill="#fff"/><circle cx="7" cy="7" r="2.5" fill="#3a4250"/></svg></span><span>48 Alder Lane, Fenwick, Pennsylvania 17000, US</span></div>
    <div class="foot-contact"><span class="ico"><svg width="14" height="14" viewBox="0 0 24 24"><path d="M6.6 10.8a15 15 0 0 0 6.6 6.6l2.2-2.2a1 1 0 0 1 1-.25 11 11 0 0 0 3.6.6 1 1 0 0 1 1 1V20a1 1 0 0 1-1 1A17 17 0 0 1 3 4a1 1 0 0 1 1-1h3.5a1 1 0 0 1 1 1 11 11 0 0 0 .6 3.6 1 1 0 0 1-.25 1z" fill="#fff"/></svg></span><span>555.014.2270</span></div>
    <div class="foot-contact"><span class="ico"><svg width="14" height="11" viewBox="0 0 24 18"><rect x="1" y="1" width="22" height="16" rx="2" fill="#fff"/><path d="M1 2l11 8 11-8" fill="none" stroke="#3a4250" stroke-width="2"/></svg></span><span>mvoss.golf@example.com</span></div>
  </div>
  <div class="foot-col" style="left:860px;width:240px">
    <h5>KEEP UPDATED</h5>
    <p style="font-size:12px;line-height:23px">Sign up for our monthly newsletter and to receive alerts on latest career opportunities.</p>
    <div class="newsletter"><span>Your Email</span><span class="go"><svg width="14" height="14" viewBox="0 0 16 16"><path d="M1 7l14-6-5 14-2-6z" fill="#fff"/></svg></span></div>
  </div>
  <div class="copyright">Copyright © 2022 MVoss, LLC All rights reserved.</div>
</footer>

</body>
</html>
```